Professional and creative business card design for recruiting service providers

Our company supports German medium-sized companies in filling vacancies promptly. For this we use social media marketing and bring our customers into the visibility.

We want a professional but also creative design for our business cards.

Please look at lindqvar-staff.de to get an impression of our CI.

Target Market(s)

Small and medium-sized companies in Germany from the industry

Industry/Entity Type

Industrie, Handwerk

Contact Information for Business Card

Name, Position, Telefonnummer, Email, Website

Colors
EE7325
F08F49
F5BC92
FAE3D3
FDF4ED

Requirements
Must have
• A picture of the employee and in the style of www.lindqvar-staff.de

```html
<!DOCTYPE html>
<html lang="de">
<head>
<meta charset="utf-8">
<title>Lindqvar Staff – Visitenkarte</title>
<link rel="stylesheet" href="https://fonts.googleapis.com/css2?family=Montserrat:wght@700&family=Arimo:wght@400;700&display=swap">
<style>
  :root {
    --bg: #e9e8e6;
    --card: #333333;
    --card-deep: #2b2b2b;
    --orange: #ee7325;
    --orange-soft: #f08f49;
    --white: #ffffff;
    --text: #e6e6e6;
  }
  * { margin: 0; padding: 0; box-sizing: border-box; }
  html, body { width: 1200px; height: 802px; overflow: hidden; }
  body {
    background: var(--bg);
    display: flex;
    align-items: center;
    justify-content: center;
    gap: 40px;
    font-family: "Arimo", Arial, sans-serif;
  }
  .card {
    position: relative;
    width: 540px;
    height: 350px;
    background: var(--card);
    overflow: hidden;
    box-shadow: 0 10px 24px rgba(0,0,0,0.18);
  }

  /* Front */
  .portrait {
    position: absolute;
    right: 0; top: 0;
    width: 250px; height: 340px;
    background: radial-gradient(ellipse at 45% 35%, #6b5548 0%, #3a3030 35%, #1f1f22 70%, #2a2a2c 100%);
  }
  .accent-band {
    position: absolute;
    left: 0; right: 0; bottom: 0;
    height: 10px;
    background: var(--orange);
  }
  .brand {
    position: absolute;
    display: flex;
    align-items: center;
    gap: 14px;
  }
  .brand-mark {
    width: 46px; height: 46px;
    background: var(--orange);
  }
  .brand-name {
    font-family: "Montserrat", Arial, sans-serif;
    font-weight: 700;
    color: var(--white);
    letter-spacing: 1.5px;
    line-height: 1.05;
  }
  .front .brand { left: 36px; top: 48px; }
  .front .brand-name { font-size: 24px; }

  .person { position: absolute; left: 36px; top: 150px; }
  .person-name {
    color: var(--orange);
    font-size: 17px;
    text-transform: uppercase;
    letter-spacing: 0.5px;
  }
  .person-role { color: var(--text); font-size: 14px; margin-top: 2px; }

  .address {
    position: absolute; left: 36px; top: 210px;
    color: var(--text); font-size: 13px; line-height: 1.3;
    font-style: normal;
  }
  .contacts {
    position: absolute; left: 36px; top: 258px;
    list-style: none;
    color: var(--text); font-size: 13px; line-height: 1.35;
  }
  .contacts li { display: flex; align-items: center; gap: 8px; }
  .contacts svg { width: 11px; height: 11px; flex: none; }

  /* Back */
  .back { background: var(--card-deep); }
  .emboss-field {
    position: absolute; inset: 0;
    background: linear-gradient(120deg, #262626 0%, #303030 45%, #4a4a4a 80%, #3a3a3a 100%);
  }
  .back .brand { left: 250px; top: 150px; }
  .back .brand-name { font-size: 22px; }
</style>
</head>
<body>

<section class="card front" aria-label="Vorderseite">
  <div class="portrait" role="img" aria-label="Porträtfoto des Mitarbeiters"></div>

  <div class="brand">
    <span class="brand-mark"></span>
    <span class="brand-name">LINDQVAR<br>STAFF</span>
  </div>

  <div class="person">
    <p class="person-name">Mats Ekholm</p>
    <p class="person-role">Manager</p>
  </div>

  <address class="address">
    Kernerstraße 42b<br>70182 Stuttgart
  </address>

  <ul class="contacts">
    <li>
      <svg viewBox="0 0 12 12"><path fill="var(--orange)" d="M2.5 1l2 2.2-1 1.3c.7 1.5 1.8 2.6 3.3 3.3l1.3-1 2.2 2-1.3 1.7C5 10.2 1.8 7 1 2.3z"/></svg>
      0170 482 1935
    </li>
    <li>
      <svg viewBox="0 0 12 12"><rect x="1" y="2.5" width="10" height="7" fill="none" stroke="var(--orange)" stroke-width="1.2"/><path d="M1 3l5 3.5L11 3" fill="none" stroke="var(--orange)" stroke-width="1.2"/></svg>
      info@lindqvar-staff.de
    </li>
    <li>
      <svg viewBox="0 0 12 12"><circle cx="6" cy="6" r="5" fill="none" stroke="var(--orange)" stroke-width="1.2"/><path d="M1 6h10M6 1c-2.5 3-2.5 7 0 10M6 1c2.5 3 2.5 7 0 10" fill="none" stroke="var(--orange)" stroke-width="1"/></svg>
      www.lindqvar-staff.de
    </li>
  </ul>

  <div class="accent-band"></div>
</section>

<section class="card back" aria-label="Rückseite">
  <div class="emboss-field" role="img" aria-label="Geprägtes Markenmuster auf dunklem Grund"></div>
  <div class="brand">
    <span class="brand-mark"></span>
    <span class="brand-name">LINDQVAR<br>STAFF</span>
  </div>
</section>

</body>
</html>
```